VOMRA Pty Ltd Business Card

Looking for a simple yet eye-catching double-sided business card design using my company logo on one side and contact details on the other.

Target Market(s)

Government

Industry/Entity Type

Communication Systems Engineering

Contact Information for Business Card

VOMRA Pty Ltd

Requirements
Nice to have
• Would be great to have a QR code so details can be scanned into contacts

```html
<!DOCTYPE html>
<html lang="en">
<head>
<meta charset="utf-8">
<title>VOMRA Pty Ltd Business Card</title>
<link href="https://fonts.googleapis.com/css2?family=Open+Sans:wght@400;700&display=swap" rel="stylesheet">
<style>
  :root {
    --stage: #1d2126;
    --card: #343d44;
    --card-edge: #2a3137;
    --ink: #ffffff;
    --emboss-light: #3c464e;
    --emboss-dark: #2b3238;
  }
  * { box-sizing: border-box; margin: 0; padding: 0; }
  html, body {
    width: 1200px; height: 780px; overflow: hidden;
    background: var(--stage);
    font-family: "Open Sans", Arial, sans-serif;
    color: var(--ink);
  }
  .stage {
    width: 1200px; height: 780px;
    display: flex; align-items: center; justify-content: center; gap: 40px;
  }
  .card {
    position: relative;
    width: 540px; height: 310px;
    background: var(--card);
    box-shadow: 0 3px 0 var(--card-edge), 0 18px 40px rgba(0,0,0,.45);
    overflow: hidden;
  }

  /* Front side */
  .card--front .brand {
    position: absolute; left: 0; right: 0; top: 50%;
    transform: translateY(-50%);
    display: flex; align-items: center; justify-content: center; gap: 22px;
  }
  .card--front .brand-dot {
    width: 54px; height: 54px; border-radius: 50%;
    border: 3px solid var(--ink);
  }
  .card--front .brand-name {
    font-weight: 700; font-size: 78px; letter-spacing: 6px; line-height: 1;
  }

  /* Back side */
  .card--back .brand {
    position: absolute; left: 34px; top: 30px;
    display: flex; align-items: center; gap: 12px;
  }
  .card--back .brand-dot {
    width: 26px; height: 26px; border-radius: 50%;
    border: 2px solid var(--ink);
  }
  .card--back .brand-name {
    font-weight: 700; font-size: 40px; letter-spacing: 3px; line-height: 1;
  }
  .contact {
    position: absolute; left: 34px; top: 110px;
    list-style: none; font-size: 12.5px; line-height: 1.45;
  }
  .contact li { display: flex; align-items: center; gap: 7px; }
  .contact .address { padding-left: 17px; margin-bottom: 2px; }
  .contact svg { width: 10px; height: 10px; flex: none; fill: var(--ink); }
  .person {
    position: absolute; right: 62px; top: 150px; text-align: right;
  }
  .person-name { font-weight: 700; font-size: 26px; line-height: 1.1; }
  .person-role { font-size: 14px; line-height: 1.3; }
  .edge-steps {
    position: absolute; right: 0; top: 196px; width: 40px; height: 114px;
  }
  .edge-steps polygon { fill: var(--ink); }
  .emboss {
    position: absolute; left: 190px; bottom: 0; width: 200px; height: 170px;
    background: radial-gradient(ellipse at 50% 60%, var(--emboss-light) 0%, var(--card) 70%);
    box-shadow: inset 0 0 0 0 var(--emboss-dark);
  }
</style>
</head>
<body>
<main class="stage">
  <section class="card card--back" aria-label="Back of card with contact details">
    <div class="brand">
      <span class="brand-dot"></span>
      <span class="brand-name">VOMRA</span>
    </div>
    <ul class="contact">
      <li class="address">14-16 Harlow Lane Redfern<br>NSW 2016 Australia</li>
      <li>
        <svg viewBox="0 0 10 10" aria-hidden="true"><path d="M2 0.5 L3.6 2.6 L2.7 3.6 Q3.8 5.9 6.3 7.3 L7.4 6.4 L9.5 8 L8.3 9.5 Q3.5 9 0.5 1.8 Z"/></svg>
        (812) 555-0147
      </li>
      <li>
        <svg viewBox="0 0 10 10" aria-hidden="true"><path d="M5 0a5 5 0 1 0 0 10A5 5 0 0 0 5 0Zm0 1c.7.6 1.2 1.9 1.3 3.4H3.7C3.8 2.9 4.3 1.6 5 1Zm-1.3 4.6h2.6C6.2 7.1 5.7 8.4 5 9 4.3 8.4 3.8 7.1 3.7 5.6ZM1.1 4.4A4 4 0 0 1 3.3 1.4 6 6 0 0 0 2.6 4.4Zm0 1.2h1.5a6 6 0 0 0 .7 3A4 4 0 0 1 1.1 5.6Zm6.3 0h1.5a4 4 0 0 1-2.2 3 6 6 0 0 0 .7-3Zm0-1.2a6 6 0 0 0-.7-3 4 4 0 0 1 2.2 3Z"/></svg>
        www.vomra.com.au
      </li>
      <li>
        <svg viewBox="0 0 10 10" aria-hidden="true"><path d="M0 2h10v6H0Zm1 1 4 3 4-3v-.2H1Z"/></svg>
        admin@vomra.com.au
      </li>
    </ul>
    <div class="emboss" role="img" aria-label="Subtle embossed decorative pattern"></div>
    <div class="person">
      <p class="person-name">Jordan Hale</p>
      <p class="person-role">Co-Founder</p>
    </div>
    <svg class="edge-steps" viewBox="0 0 40 114" aria-hidden="true">
      <polygon points="40,0 40,114 28,114 28,100 22,100 22,82 16,82 16,62 10,62 10,40 4,40 4,18 0,18 0,0"/>
    </svg>
  </section>

  <section class="card card--front" aria-label="Front of card with company name">
    <div class="brand">
      <span class="brand-dot"></span>
      <span class="brand-name">VOMRA</span>
    </div>
  </section>
</main>
</body>
</html>
```